Website for my photography business

I need a website for my photography business, Bram Kellet Photography. I need a website that has a landing page with a cover photo of each kind of photography I do. For example, Nature, Weddings, Portraits and Architecture. I want it so that when someone comes onto my website they have to choose which kind of photography page they want to visit. So if they click on the wedding photo it will open to a page with my wedding portfolio images and a contact me button. If they choose nature photography I want them to be redirected to an e-commerce section where they can purchase prints. Architecture and Portraits should open up to their respective portfolios with about me and contact info. I like this kind of format because I want people who come to my website for a specific type of photography to be able to be directed there easily without having to look at a mix of other kinds of photography. I will provide a few files to use as placeholders. I have already purchased the bramkelletphotography.example domain name. A Wix website would be great because I am most familiar with it but I am open to anything.

Industry/Entity Type

Photographer

Number of Pages Required

5+ page

Requirements
Must have
• Landing Page and e-commerce

```html
<!DOCTYPE html>
<html lang="en">
<head>
<meta charset="UTF-8">
<title>Bram Kellet Photography</title>
<link rel="stylesheet" href="https://fonts.googleapis.com/css2?family=Dancing+Script:wght@400;700&family=Libre+Baskerville:ital@0;1&family=Jost:wght@400;500&display=swap">
<style>
  :root {
    --ink: #2b2b2b;
    --ink-soft: #444;
    --muted: #b5b5b5;
    --rule: #bdbdbd;
    --paper: #ffffff;
    --sky-top: #a9c0c8;
    --sky-mid: #c9d3d0;
    --stone: #9c7f58;
    --stone-dark: #3c4650;
    --mint: #4bd29f;
    --navy: #26384a;
  }
  * { box-sizing: border-box; margin: 0; padding: 0; }
  html, body { width: 1100px; height: 1200px; overflow: hidden; background: var(--paper); }
  body { position: relative; color: var(--ink); font-family: "Libre Baskerville", Georgia, serif; }

  .site-header {
    position: absolute; left: 217px; top: 39px; width: 669px; height: 130px;
    border: 2px solid var(--ink); text-align: center;
  }
  .brand-title {
    font-family: "Dancing Script", cursive; font-weight: 400;
    font-size: 46px; line-height: 1; margin-top: 6px; color: var(--ink);
  }
  .brand-tagline {
    font-family: "Dancing Script", cursive; font-size: 19px; color: var(--ink-soft);
    margin-top: 2px;
  }
  .main-nav {
    display: flex; justify-content: center; margin-top: 12px;
  }
  .main-nav a {
    font-style: italic; font-size: 13px; color: var(--ink); text-decoration: none;
    padding: 6px 12px; border-left: 1px solid var(--rule);
  }
  .main-nav a:first-child { border-left: none; }
  .main-nav a.is-current { color: var(--muted); }

  .hero {
    position: absolute; left: 0; top: 221px; width: 1100px; height: 483px; overflow: hidden;
  }
  .hero-photo {
    position: absolute; inset: 0;
    background:
      linear-gradient(100deg, transparent 0 60%, rgba(156,127,88,0.0) 60%),
      linear-gradient(90deg, var(--sky-mid) 0%, #cfd6d1 45%, var(--sky-top) 70%, var(--stone) 78%, #b79a6e 90%, var(--sky-top) 100%);
  }
  .hero-photo::after {
    content: ""; position: absolute; left: 0; right: 0; top: 0; height: 100%;
    background: linear-gradient(180deg, rgba(169,192,200,0.35) 0%, transparent 50%, rgba(60,70,80,0.15) 100%);
  }
  .hero-caption {
    position: absolute; left: 437px; top: 117px; width: 225px; height: 178px;
    border: 1px solid rgba(255,255,255,0.95);
    display: flex; align-items: center; justify-content: center;
  }
  .hero-caption h2 {
    font-family: "Libre Baskerville", Georgia, serif; font-weight: 400;
    font-size: 27px; color: #fff; letter-spacing: -0.5px;
  }
  .hero-arrow { position: absolute; top: 226px; }
  .hero-arrow.prev { left: 80px; }
  .hero-arrow.next { left: 1003px; }
  .hero-dots { position: absolute; top: 446px; left: 531px; display: flex; gap: 10px; }
  .hero-dots span { width: 5px; height: 5px; border-radius: 50%; background: rgba(255,255,255,0.55); }
  .hero-dots span.is-active { background: rgba(150,150,150,0.7); }

  .about-card {
    position: absolute; left: 435px; top: 768px; width: 229px; height: 225px;
    background: var(--mint); text-align: center;
  }
  .about-portrait {
    position: absolute; left: 55px; top: 25px; width: 120px; height: 120px; border-radius: 50%;
    background: radial-gradient(circle at 50% 40%, #e6e6e6, #a8a8a8);
    border: 2px solid #d8f3e8;
  }
  .about-quote {
    position: absolute; left: 145px; top: 6px; font-family: Georgia, serif; font-weight: 700;
    font-size: 64px; line-height: 1; color: var(--navy);
  }
  .about-name {
    position: absolute; left: 0; right: 0; top: 151px;
    font-family: "Dancing Script", cursive; font-weight: 700; font-size: 29px; color: var(--navy);
  }
  .about-line {
    position: absolute; left: 0; right: 0; top: 188px;
    font-family: "Jost", sans-serif; font-size: 12px; color: #fff;
  }

  .contact-button {
    position: absolute; left: 505px; top: 1044px; width: 90px; height: 22px;
    display: flex; align-items: center; justify-content: center; gap: 4px;
    font-family: "Jost", sans-serif; font-weight: 500; font-size: 10.5px; letter-spacing: 0.5px; color: var(--ink);
  }

  .site-footer { position: absolute; left: 0; top: 1140px; width: 1100px; text-align: center; }
  .copyright { font-style: italic; font-size: 10px; color: var(--ink-soft); }
  .social-links { display: flex; justify-content: center; gap: 14px; margin-top: 24px; }
  .social-links a {
    font-family: "Jost", sans-serif; font-size: 11px; font-weight: 500; color: #111; text-decoration: none;
  }
</style>
</head>
<body>
  <header class="site-header">
    <h1 class="brand-title">Bram Kellet Photography</h1>
    <p class="brand-tagline">Creating extraordinary images that last infinitely</p>
    <nav class="main-nav">
      <a href="#">Home</a>
      <a href="#" class="is-current">Architecture</a>
      <a href="#">Portraits</a>
      <a href="#">Weddings</a>
      <a href="#">Nature</a>
      <a href="#">Contact me</a>
    </nav>
  </header>

  <section class="hero">
    <div class="hero-photo" role="img" aria-label="Photograph of a gothic clock tower against a pale blue sky"></div>
    <div class="hero-caption"><h2>Architecture</h2></div>
    <svg class="hero-arrow prev" width="18" height="34" viewBox="0 0 18 34"><polyline points="17,1 1,17 17,33" fill="none" stroke="#333" stroke-width="1.5"/></svg>
    <svg class="hero-arrow next" width="18" height="34" viewBox="0 0 18 34"><polyline points="1,1 17,17 1,33" fill="none" stroke="#333" stroke-width="1.5"/></svg>
    <div class="hero-dots"><span class="is-active"></span><span></span><span></span></div>
  </section>

  <section class="about-card">
    <div class="about-portrait" role="img" aria-label="Portrait photo of the photographer"></div>
    <div class="about-quote">”</div>
    <p class="about-name">Bram Kellet</p>
    <p class="about-line">Why I can do the job for you.</p>
  </section>

  <a class="contact-button" href="#">
    <svg width="14" height="10" viewBox="0 0 14 10"><rect x="0.5" y="0.5" width="13" height="9" fill="none" stroke="#222"/><polyline points="0.5,0.5 7,6 13.5,0.5" fill="none" stroke="#222"/></svg>
    Contact me!
  </a>

  <footer class="site-footer">
    <p class="copyright">© 2020 by Bram Kellet.</p>
    <div class="social-links">
      <a href="#">Linkfeed</a>
      <a href="#">Chirper</a>
      <a href="#">Snapbook</a>
    </div>
  </footer>
</body>
</html>
```